PPE EQIUPMENT

WE WOULD LIKE TO PRODUCE 2 DIFFERENT BANNERS TO BE PLACED OUTSIDE OF OUR WAREHOUSE TO ADVERTISE THAT WE HAVE FACE MASKS, HAND SANITISERS, DISINFECTANT SPRAY, FACE SHIELDS AND HAND SOAP. THE SIZE OF EACH BANNER WILL BE , portrait to be (W) 140 cm x (H) 250 cm, with 4 x eyelets. THE BANNER IS TO STATE PPE EQUIPMENT AVAILABLE HERE AND SHOW OUR PHONE NUMBER 0208-417-2953. FINALLY WE WILL REQUIRE SOME IMAGES OF THE PRODUCTS IF YOU CAN SUPPLY THESE. THANKS

```html
<!DOCTYPE html>
<html lang="en">
<head>
<meta charset="utf-8">
<title>Northgate Furniture – PPE Equipment Available Here</title>
<link rel="stylesheet" href="https://fonts.googleapis.com/css2?family=Barlow:wght@400;500;600&family=Open+Sans:wght@800&display=swap">
<style>
  :root {
    --brand-blue: #2a4589;
    --brand-red: #b41535;
    --brand-navy: #2c2e5c;
    --accent-yellow: #ffe200;
    --text-white: #ffffff;
    --scene-dark: #2a0a10;
  }
  * { margin: 0; padding: 0; box-sizing: border-box; }
  html, body { width: 672px; height: 1200px; overflow: hidden; background: var(--brand-blue); }
  .banner { position: relative; width: 672px; height: 1200px; overflow: hidden; }
  .top-stripe { height: 10px; background: var(--brand-red); }
  .brand-band {
    height: 174px; background: var(--brand-blue); color: var(--text-white);
    font-family: "Barlow", sans-serif; text-align: center;
    display: flex; flex-direction: column; justify-content: center; padding-top: 4px;
  }
  .brand-name { font-weight: 500; font-size: 55px; letter-spacing: 1.5px; line-height: 1; white-space: nowrap; }
  .brand-tagline { font-weight: 400; font-size: 31px; letter-spacing: 1.2px; line-height: 1; margin-top: 10px; }
  .headline-band {
    height: 185px; background: var(--brand-red); color: var(--text-white);
    font-family: "Open Sans", sans-serif; font-weight: 800; text-align: center;
    display: flex; flex-direction: column; justify-content: center;
  }
  .headline-line { font-size: 59px; line-height: 1.35; letter-spacing: 1px; white-space: nowrap; }
  .headline-highlight { color: var(--accent-yellow); }
  .product-showcase { display: block; width: 672px; height: 697px; }
  .product-caption {
    font-family: "Barlow", sans-serif; font-weight: 600; font-size: 22px;
    letter-spacing: 1.5px; fill: var(--text-white); text-anchor: middle;
  }
  .contact-band {
    height: 120px; background: var(--brand-blue); color: var(--accent-yellow);
    font-family: "Open Sans", sans-serif; font-weight: 800; font-size: 64px;
    text-align: center; line-height: 120px; letter-spacing: 1px;
  }
  .bottom-stripe { height: 14px; background: var(--accent-yellow); border-top: 4px solid var(--brand-red); }
</style>
</head>
<body>
<main class="banner">
  <div class="top-stripe"></div>
  <header class="brand-band">
    <div class="brand-name">NORTHGATE FURNITURE</div>
    <div class="brand-tagline">TRADE FURNITURE SOLUTIONS</div>
  </header>
  <section class="headline-band">
    <div class="headline-line">PPE EQUIPMENT</div>
    <div class="headline-line">AVAILABLE <span class="headline-highlight">HERE</span></div>
  </section>
  <svg class="product-showcase" viewBox="0 0 672 697" xmlns="http://www.w3.org/2000/svg">
    <defs>
      <radialGradient id="scene-glow" cx="0.5" cy="0.35" r="0.75">
        <stop offset="0" stop-color="#3a6f78"/>
        <stop offset="0.45" stop-color="#3a1820"/>
        <stop offset="1" stop-color="#2a0a10"/>
      </radialGradient>
    </defs>
    <rect class="scene-backdrop" width="672" height="697" fill="url(#scene-glow)" role="img" aria-label="Close-up illustration of teal virus particles on a dark red background"/>

    <g class="product-tile" role="img" aria-label="Photo of a pale blue disposable face mask">
      <circle cx="171" cy="166" r="107" fill="var(--accent-yellow)"/>
      <circle cx="163" cy="158" r="107" fill="var(--brand-red)"/>
      <text class="product-caption" x="163" y="166">FACE MASKS</text>
    </g>
    <g class="product-tile" role="img" aria-label="Photo of a pump bottle of aloe hand sanitiser">
      <circle cx="517" cy="171" r="109" fill="var(--accent-yellow)"/>
      <circle cx="509" cy="163" r="109" fill="var(--brand-navy)"/>
      <text class="product-caption" x="509" y="158">HAND</text>
      <text class="product-caption" x="509" y="184">SANITISER</text>
    </g>
    <g class="product-tile" role="img" aria-label="Photo of a lemon scented disinfectant spray can">
      <circle cx="324" cy="356" r="110" fill="var(--accent-yellow)"/>
      <circle cx="332" cy="364" r="110" fill="var(--brand-red)"/>
      <text class="product-caption" x="332" y="359">DISINFECTANT</text>
      <text class="product-caption" x="332" y="385">SPRAY</text>
    </g>
    <g class="product-tile" role="img" aria-label="Photo of a clear plastic face shield on a display head">
      <circle cx="162" cy="540" r="110" fill="var(--accent-yellow)"/>
      <circle cx="170" cy="532" r="110" fill="var(--brand-navy)"/>
      <text class="product-caption" x="170" y="540">FACE SHIELDS</text>
    </g>
    <g class="product-tile" role="img" aria-label="Photo of a pump bottle of hand and body soap">
      <circle cx="498" cy="540" r="110" fill="var(--accent-yellow)"/>
      <circle cx="506" cy="532" r="110" fill="var(--brand-red)"/>
      <text class="product-caption" x="506" y="540">HAND SOAP</text>
    </g>
  </svg>
  <footer class="contact-band">0208-417-2953</footer>
  <div class="bottom-stripe"></div>
</main>
</body>
</html>
```